Improve Wine Bottle Label, Glass Printed Naked Lady, Elegant, Classy, Professional

We are transitioning our labelling method over to glass screen-printing.We have an existing label (attached image1 -ai also attached) that we think is cool, but moving forward we would like a more professional looking design that is classy, artsy, but still high impact (one very rough idea is attached). The bottle is remaining the same size. The cap is the same pink colour. Title of wine is Saffron Kestrel' Front Text needs to include:2018 MontepulcianoEden Valley - Barossa The graphic must contain a tasteful (arty) and attractive naked woman. Design colours that are preferred are:Hot Pink - as seen in imageDark Blue - as seen in imageMatte White** Note that colours are single, shading etc is not easily possible due to the screen printing method. - view process on our instagram page. https://www.pictura.example/dalrowvino/- please also look at this page to see our other recent labels, so ascertain our style/audience.You do not need to have all the colours, if your submission looks great with 1 or 2. feel free to keep it this way. Dimensions.The glass printer can print within 10mm of the base of the bottle, and 10mm of the shoulder of the bottle. Height 150mmIt can print the full circumference of the bottle up to approx 30mm gap. (Max 208mm) - see our gold label on the instagram page. - however, imagine this bottle in a store - we need customers to be able to see the image and title on one side. So if you decide to wrap around the bottle, it needs to achieve the requirements whilst only seeing the Title side of the bottle. We have found this to be about 90mm wide maximum.

Target Market(s)

Wine Consumers

Industry/Entity Type

Winery

Font styles to use
Serif
Sans Serif

Colors
e34297
3176b5
ffffff

Requirements
Must have
• Colours, Title, Text - as stated
• Naked arty woman
• Single colours - NO SHADING
Nice to have
• Our Logo integrated smoothly - only do this if you can do it well.

```html
<!DOCTYPE html>
<html lang="en">
<head>
<meta charset="utf-8">
<title>Saffron Kestrel – 2018 Montepulciano</title>
<link rel="stylesheet" href="https://fonts.googleapis.com/css2?family=Josefin+Sans:wght@300;400&family=Cormorant+Garamond:wght@500&display=swap">
<style>
  :root {
    --page: #ffffff;
    --glass: #1b0f14;
    --glass-edge: #0b0507;
    --glass-sheen: #3a2a30;
    --capsule: #c2349a;
    --capsule-light: #bf68b0;
    --pink: #e34297;
    --hot-pink: #ee1f86;
    --gold: #d6b36a;
    --gold-deep: #a8823f;
    --matte-white: #ffffff;
  }
  html, body {
    margin: 0;
    padding: 0;
    width: 756px;
    height: 1200px;
    overflow: hidden;
    background: var(--page);
  }
  .bottle-pair {
    display: block;
    width: 756px;
    height: 1200px;
  }
  .wine-title {
    font-family: "Josefin Sans", sans-serif;
    font-weight: 400;
    font-size: 44px;
    fill: var(--matte-white);
  }
  .vintage-line {
    font-family: "Cormorant Garamond", serif;
    font-weight: 500;
    font-size: 23px;
    fill: var(--gold);
  }
  .winery-mark-name {
    font-family: "Josefin Sans", sans-serif;
    font-weight: 400;
    font-size: 12px;
    letter-spacing: 1px;
    fill: var(--matte-white);
  }
</style>
</head>
<body>
<svg class="bottle-pair" viewBox="0 0 756 1200" xmlns="http://www.w3.org/2000/svg">
  <defs>
    <linearGradient id="glass-body" x1="0" x2="1" y1="0" y2="0">
      <stop offset="0" stop-color="var(--glass-edge)"/>
      <stop offset="0.3" stop-color="var(--glass)"/>
      <stop offset="0.55" stop-color="var(--glass-sheen)"/>
      <stop offset="0.75" stop-color="var(--glass)"/>
      <stop offset="1" stop-color="var(--glass-edge)"/>
    </linearGradient>
    <linearGradient id="gold-rule" x1="0" x2="1">
      <stop offset="0" stop-color="var(--gold-deep)"/>
      <stop offset="0.5" stop-color="var(--gold)"/>
      <stop offset="1" stop-color="var(--gold-deep)"/>
    </linearGradient>
    <radialGradient id="figure-pink" cx="0.5" cy="0.45" r="0.55">
      <stop offset="0" stop-color="var(--pink)" stop-opacity="0.75"/>
      <stop offset="0.6" stop-color="var(--pink)" stop-opacity="0.4"/>
      <stop offset="1" stop-color="var(--pink)" stop-opacity="0"/>
    </radialGradient>
    <radialGradient id="figure-gold" cx="0.5" cy="0.45" r="0.55">
      <stop offset="0" stop-color="var(--gold)" stop-opacity="0.75"/>
      <stop offset="0.6" stop-color="var(--gold)" stop-opacity="0.4"/>
      <stop offset="1" stop-color="var(--gold)" stop-opacity="0"/>
    </radialGradient>
  </defs>

  <!-- Pink variant -->
  <g class="bottle bottle--pink">
    <path class="bottle-glass" fill="url(#glass-body)"
      d="M184 235 L184 300 C184 365 100 372 100 445 L100 1130 Q100 1145 115 1145 L348 1145 Q362 1145 362 1130 L362 445 C362 372 272 365 272 300 L272 235 Z"/>
    <g class="capsule">
      <rect x="178" y="56" width="96" height="186" rx="6" fill="var(--capsule)"/>
      <rect x="178" y="56" width="38" height="186" rx="6" fill="var(--capsule-light)"/>
    </g>
    <g class="winery-mark">
      <circle cx="200" cy="552" r="17" fill="none" stroke="var(--matte-white)" stroke-width="1.5"/>
      <text class="winery-mark-name" x="222" y="556">Dalrow</text>
    </g>
    <ellipse class="figure-artwork" cx="202" cy="775" rx="78" ry="180"
      fill="url(#figure-pink)" role="img" aria-label="Single-line pink drawing of a dancing nude woman with flowing hair, standing on one leg"/>
    <text class="wine-title" x="322" y="945" transform="rotate(-90 322 945)" textLength="435" lengthAdjust="spacing">SAFFRON KESTREL</text>
    <text class="vintage-line" x="127" y="980" textLength="208" lengthAdjust="spacing">2018 Montepulciano</text>
    <text class="vintage-line" x="127" y="1006" textLength="209" lengthAdjust="spacing">Eden Valley - Barossa</text>
    <rect class="band-colour" x="96" y="1020" width="270" height="9" fill="var(--pink)"/>
    <rect class="band-gold" x="96" y="1032" width="270" height="3" fill="url(#gold-rule)"/>
  </g>

  <!-- Gold variant -->
  <g class="bottle bottle--gold" transform="translate(290 0)">
    <path class="bottle-glass" fill="url(#glass-body)"
      d="M184 235 L184 300 C184 365 100 372 100 445 L100 1130 Q100 1145 115 1145 L348 1145 Q362 1145 362 1130 L362 445 C362 372 272 365 272 300 L272 235 Z"/>
    <g class="capsule">
      <rect x="178" y="56" width="96" height="186" rx="6" fill="var(--capsule)"/>
      <rect x="178" y="56" width="38" height="186" rx="6" fill="var(--capsule-light)"/>
    </g>
    <g class="winery-mark">
      <circle cx="200" cy="552" r="17" fill="none" stroke="var(--matte-white)" stroke-width="1.5"/>
      <text class="winery-mark-name" x="222" y="556">Dalrow</text>
    </g>
    <ellipse class="figure-artwork" cx="202" cy="775" rx="78" ry="180"
      fill="url(#figure-gold)" role="img" aria-label="Single-line gold drawing of a dancing nude woman with flowing hair, standing on one leg"/>
    <text class="wine-title" x="322" y="945" transform="rotate(-90 322 945)" textLength="435" lengthAdjust="spacing">SAFFRON KESTREL</text>
    <text class="vintage-line" x="127" y="980" textLength="208" lengthAdjust="spacing">2018 Montepulciano</text>
    <text class="vintage-line" x="127" y="1006" textLength="209" lengthAdjust="spacing">Eden Valley - Barossa</text>
    <rect class="band-colour" x="96" y="1020" width="270" height="9" fill="var(--hot-pink)"/>
    <rect class="band-gold" x="96" y="1032" width="270" height="3" fill="url(#gold-rule)"/>
  </g>
</svg>
</body>
</html>
```